Stylish Business Cards Wanted

- DOUBLE SIDED Design Required -

High end, edgy cards for a corporate and personal stylist. Must include logo,
Name: Belinda Harwick
Title: Director and Stylist
telephone : +61 8 7142 5809
email: belinda@theloombriefing.example
website: theloombriefing.example
Tag: Corporate Workwear & Uniform Specialist | Personal Stylist
Would like nice icons for telephone, email, website

Target Market(s)

Businesses wanting stylish uniforms, people wanting stylish wardrobes

Industry/Entity Type

Corporate Workwear Stylist

Contact Information for Business Card

I would like black, white and gold foiling incorporated in the design - possibly a touch of the other colours on my branding guide attached Name: Belinda Harwick Title: Director and Stylist telephone : +61 8 7142 5809 email: belinda@theloombriefing.example website: theloombriefing.example Tag: Corporate Workwear & Uniform Specialist | Personal Stylist Would like nice icons for telephone, email, website

Font styles to use
Other font styles liked:
• Raleway

Colors

Designer to choose colors to be used in the design.

Requirements
Must have
• Gold foil accents

```html
<!DOCTYPE html>
<html lang="en">
<head>
<meta charset="utf-8">
<title>The Loom Briefing – Business Cards</title>
<link rel="stylesheet" href="https://fonts.googleapis.com/css2?family=Lato:wght@400;700&display=swap">
<style>
  :root {
    --ink: #231f20;
    --paper: #ffffff;
    --gold: #e3b95a;
    --backdrop: #e9e6e1;
    --shadow: rgba(0, 0, 0, 0.22);
  }
  * { box-sizing: border-box; margin: 0; padding: 0; }
  html, body {
    width: 1200px;
    height: 900px;
    overflow: hidden;
    background: var(--backdrop);
    font-family: "Lato", Arial, sans-serif;
  }
  .sheet {
    position: relative;
    width: 1200px;
    height: 900px;
  }
  .card {
    position: absolute;
    left: 250px;
    width: 700px;
    height: 400px;
    overflow: hidden;
    box-shadow: 0 6px 18px var(--shadow);
  }
  /* Front side */
  .card--front {
    top: 35px;
    background: var(--ink);
  }
  .card--front .brand-name {
    position: absolute;
    left: 0;
    right: 0;
    top: 50%;
    transform: translateY(-50%);
    text-align: center;
    color: var(--paper);
    font-weight: 700;
    font-size: 46px;
    letter-spacing: 10px;
    text-transform: uppercase;
  }
  /* Back side */
  .card--back {
    top: 465px;
    background: var(--paper);
  }
  .card__wave {
    position: absolute;
    inset: 0;
  }
  .holder {
    position: absolute;
    left: 48px;
    top: 62px;
    width: 300px;
  }
  .holder__name {
    color: var(--gold);
    font-weight: 700;
    font-size: 26px;
    letter-spacing: 0.5px;
    text-transform: uppercase;
    line-height: 1.1;
    white-space: nowrap;
  }
  .holder__title {
    color: var(--ink);
    font-size: 17px;
    margin-top: 4px;
  }
  .back-brand {
    position: absolute;
    right: 44px;
    top: 40px;
    display: flex;
    align-items: flex-start;
    gap: 12px;
  }
  .back-brand__mark {
    width: 14px;
    height: 14px;
    margin-top: 8px;
    background: var(--gold);
    flex: none;
  }
  .back-brand__name {
    color: var(--ink);
    font-weight: 700;
    font-size: 26px;
    line-height: 1.2;
    letter-spacing: 4px;
    text-transform: uppercase;
  }
  .back-brand__line { display: block; }
  .contacts {
    position: absolute;
    left: 48px;
    top: 178px;
    list-style: none;
  }
  .contacts__item {
    display: flex;
    align-items: center;
    gap: 12px;
    color: var(--ink);
    font-size: 18px;
    line-height: 28px;
  }
  .contacts__icon {
    width: 18px;
    height: 18px;
    flex: none;
  }
  .tagline {
    position: absolute;
    right: 30px;
    bottom: 22px;
    color: var(--paper);
    font-size: 16px;
    letter-spacing: 0.3px;
  }
  .tagline__dot {
    color: var(--gold);
    margin: 0 8px;
  }
</style>
</head>
<body>
<main class="sheet">

  <section class="card card--front" aria-label="Business card front">
    <p class="brand-name">The Loom Briefing</p>
  </section>

  <section class="card card--back" aria-label="Business card back">
    <svg class="card__wave" viewBox="0 0 700 400" width="700" height="400" aria-hidden="true">
      <path fill="var(--gold)" d="M0,318 C190,326 370,285 480,205 C390,300 210,346 0,346 Z"/>
      <path fill="var(--ink)" d="M0,346 C210,346 400,300 520,205 C590,152 650,140 700,134 L700,400 L0,400 Z"/>
    </svg>

    <div class="holder">
      <p class="holder__name">Belinda Harwick</p>
      <p class="holder__title">Director and Stylist</p>
    </div>

    <div class="back-brand">
      <span class="back-brand__mark"></span>
      <p class="back-brand__name">
        <span class="back-brand__line">The Loom</span>
        <span class="back-brand__line">Briefing</span>
      </p>
    </div>

    <ul class="contacts">
      <li class="contacts__item">
        <svg class="contacts__icon" viewBox="0 0 24 24" aria-hidden="true">
          <path fill="var(--gold)" d="M6.6 10.8a15.1 15.1 0 0 0 6.6 6.6l2.2-2.2a1 1 0 0 1 1-.25 11.4 11.4 0 0 0 3.6.57 1 1 0 0 1 1 1V20a1 1 0 0 1-1 1A17 17 0 0 1 3 4a1 1 0 0 1 1-1h3.5a1 1 0 0 1 1 1c0 1.25.2 2.450.57 3.57a1 1 0 0 1-.25 1z"/>
        </svg>
        <span>+61 8 7142 5809</span>
      </li>
      <li class="contacts__item">
        <svg class="contacts__icon" viewBox="0 0 24 24" aria-hidden="true">
          <rect x="2" y="5" width="20" height="14" fill="var(--gold)"/>
          <path d="M2 5 L12 13 L22 5" fill="none" stroke="var(--paper)" stroke-width="1.6"/>
        </svg>
        <span>belinda@theloombriefing.example</span>
      </li>
      <li class="contacts__item">
        <svg class="contacts__icon" viewBox="0 0 24 24" aria-hidden="true">
          <g fill="none" stroke="var(--gold)" stroke-width="1.8">
            <circle cx="12" cy="12" r="9.5"/>
            <ellipse cx="12" cy="12" rx="4" ry="9.5"/>
            <line x1="2.5" y1="12" x2="21.5" y2="12"/>
            <line x1="4" y1="7" x2="20" y2="7"/>
            <line x1="4" y1="17" x2="20" y2="17"/>
          </g>
        </svg>
        <span>theloombriefing.example</span>
      </li>
    </ul>

    <p class="tagline">Corporate Workwear &amp; Uniform Specialist<span class="tagline__dot">●</span>Personal Stylist</p>
  </section>

</main>
</body>
</html>
```